Satchel & Sundial needs new business card design

I need a new business card design. I'm looking for out-of-the-box design which represents the freedom of being a location independent entrepreneur.
I offer coaching, retreats and trips.
I would like to see designs with and without the photo.
Colors I use are black (#000000), green (#25A796) and brown (#D7C38C)
Website satchelandsundial.example

Target Market(s)

location independent entrepreneurs, digital nomads, people looking to swap the 9 to 5 for a lifestyle business

Industry/Entity Type

Business

Contact Information for Business Card

Dorota Falkner
Your Lifestyle Business Coach, Retreat & Trip Leader
http://satchelandsundial.example
hello@satchelandsundial.example
Live a life you don't need a holiday from

Font styles to use
Serif
Sans Serif

Requirements
Must have
• One side should contain only the logo. I would also consider having the "Live a life you don't need a holiday from" on that side too (depending on how it looks)
• Please show both sides on the designs.

```html
<!DOCTYPE html>
<html lang="en">
<head>
<meta charset="utf-8">
<title>Satchel &amp; Sundial — Business Card</title>
<link rel="stylesheet" href="https://fonts.googleapis.com/css2?family=Lora:wght@400&family=Montserrat:wght@400;600&display=swap">
<style>
  :root {
    --ink: #000000;
    --green: #25A796;
    --sand: #D7C38C;
    --paper: #ffffff;
    --stage: #e6e7e8;
    --stage-line: #231f20;
  }
  * { box-sizing: border-box; margin: 0; padding: 0; }
  html, body { width: 1200px; height: 999px; overflow: hidden; background: var(--paper); }
  .canvas { position: relative; width: 1200px; height: 999px; }
  .stage {
    position: absolute; left: 0; top: 72px; width: 1200px; height: 927px;
    background: var(--stage); border: 1px solid var(--stage-line);
  }
  .card {
    position: absolute; top: 166px; width: 424px; height: 740px;
    background: var(--paper);
    box-shadow: 8px 10px 10px rgba(0,0,0,0.35);
    text-align: center; color: var(--ink);
    font-family: "Montserrat", sans-serif;
  }
  .card--front { left: 158px; }
  .card--back { left: 618px; }
  .portrait {
    display: block; width: 424px; height: 364px;
    background: linear-gradient(160deg, #6f8a4c 0%, #8a7a52 40%, #5d6a3a 70%, #7f98b8 100%);
  }
  .accent-band { height: 5px; background: var(--green); }
  .brand {
    font-family: "Montserrat", sans-serif; font-weight: 600;
    font-size: 30px; letter-spacing: 1px; text-transform: uppercase;
    color: var(--ink);
  }
  .card--front .brand { margin-top: 62px; }
  .card--back .brand { position: absolute; left: 0; right: 0; top: 330px; }
  .brand-dot {
    display: inline-block; width: 12px; height: 12px; border-radius: 50%;
    background: var(--green); margin-left: 8px; vertical-align: middle;
  }
  .person-name {
    font-family: "Lora", serif; font-weight: 400; font-size: 30px;
    color: var(--green); margin-top: 50px; line-height: 1.1;
  }
  .roles { font-size: 17.5px; line-height: 23px; margin-top: 4px; }
  .contact-icons { margin-top: 14px; height: 14px; display: flex; justify-content: center; gap: 6px; }
  .contact-list { list-style: none; font-size: 18px; line-height: 23.5px; margin-top: 14px; }
  .contact-list .domain { color: var(--green); }
  .motto {
    position: absolute; left: 0; right: 0; top: 584px;
    font-size: 19.5px; line-height: 26px; text-transform: uppercase; letter-spacing: 0.3px;
  }
</style>
</head>
<body>
<div class="canvas">
  <div class="stage"></div>

  <section class="card card--front">
    <div class="portrait" role="img" aria-label="Portrait photo of the coach sitting on a rustic fence among trees and greenery, holding a small chalkboard sign"></div>
    <div class="accent-band"></div>
    <div class="brand">Satchel &amp; Sundial<span class="brand-dot"></span></div>
    <h1 class="person-name">Dorota Falkner</h1>
    <p class="roles">Your Lifestyle Business Coach<br>Retreat &amp; Trip Leader</p>
    <div class="contact-icons" aria-hidden="true">
      <svg width="12" height="14" viewBox="0 0 12 14"><path d="M3 1 L5 4 L4 5.5 C5 8 6 9.5 8 10.5 L9.5 9.5 L11 12 L9 13.5 C5 13 2 8 1.5 3 Z" fill="none" stroke="#25A796" stroke-width="1.2"/></svg>
      <svg width="14" height="14" viewBox="0 0 14 14"><rect x="1" y="3.5" width="12" height="8" fill="none" stroke="#25A796" stroke-width="1.2"/><path d="M1 3.5 L7 8 L13 3.5" fill="none" stroke="#25A796" stroke-width="1.2"/></svg>
      <svg width="14" height="14" viewBox="0 0 14 14"><circle cx="7" cy="7" r="5.8" fill="none" stroke="#25A796" stroke-width="1.1"/><ellipse cx="7" cy="7" rx="2.5" ry="5.8" fill="none" stroke="#25A796" stroke-width="1"/><path d="M1.2 7 H12.8 M2 4 H12 M2 10 H12" stroke="#25A796" stroke-width="0.9"/></svg>
    </div>
    <ul class="contact-list">
      <li>+330 1470-5521</li>
      <li>hello@satchelandsundial.example</li>
      <li>www.<span class="domain">satchelandsundial</span>.example</li>
    </ul>
  </section>

  <section class="card card--back">
    <div class="brand">Satchel &amp; Sundial<span class="brand-dot"></span></div>
    <p class="motto">Live a life you don’t<br>need a holiday from</p>
  </section>
</div>
</body>
</html>
```